Meridale Bed Company Needs Business Card

Looking for a very nice looking business card. Creative but not extravagant. We sell beds and pillows across the U.S. and need something professional but catchy. I have attached the logo.

Name : Devin Holt
Title : President
Phone : (800) 471-2960
Email: sleep@quilmora.com
Website: www.quilmora.com

Can be single-sided or double-sided
horizontal or vertical

Can use Blues/Greys

Target Market(s)

Mass Market

Industry/Entity Type

Retail

Contact Information for Business Card

Name : Devin Holt
Title : President
Phone : (800) 471-2960
Email: sleep@quilmora.com
Website: www.quilmora.com

Requirements
Must have
• Clean, Modern, Smooth
• Can use Blues/Greys
• On the other side without the information - have something simple like www.quilmora.com or our logo
Nice to have
• Surprise me
Should not have
• Nothing crazy, nothing cluttered

```html
<!DOCTYPE html>
<html lang="en">
<head>
<meta charset="utf-8">
<title>Quilmora Business Cards</title>
<link href="https://fonts.googleapis.com/css2?family=Montserrat:wght@300;400;500;600&display=swap" rel="stylesheet">
<style>
  :root {
    --backdrop: #e6e7e8;
    --brand-blue: #2ea3dc;
    --card-white: #ffffff;
    --card-graphite: #3a3a3c;
    --card-black: #000000;
    --ink-dark: #2b2b2b;
    --ink-light: #ffffff;
    --rule-light: #c9c9c9;
    --rule-dark: #5a5a5a;
  }
  * { margin: 0; padding: 0; box-sizing: border-box; }
  html, body { width: 1200px; height: 929px; overflow: hidden; }
  body {
    background: var(--backdrop);
    font-family: "Montserrat", sans-serif;
    position: relative;
  }
  .card {
    position: absolute;
    width: 243px;
    height: 426px;
    border-radius: 17px;
    overflow: hidden;
    box-shadow: 0 4px 10px rgba(0,0,0,0.18);
  }
  .card--front-white { left: 346px; top: 28px; background: var(--card-white); color: var(--ink-dark); }
  .card--back-graphite { left: 614px; top: 28px; background: var(--card-graphite); }
  .card--front-black { left: 346px; top: 476px; background: var(--card-black); color: var(--ink-light); }
  .card--back-black { left: 614px; top: 476px; background: var(--card-black); }

  .wordmark {
    position: absolute;
    left: 0; right: 0;
    text-align: center;
    font-family: "Montserrat", sans-serif;
    font-weight: 300;
    font-size: 46px;
    letter-spacing: 1px;
    color: var(--brand-blue);
    line-height: 1;
  }
  .card--front-white .wordmark,
  .card--front-black .wordmark { top: 30px; }
  .card--back-graphite .wordmark,
  .card--back-black .wordmark { top: 190px; }

  .contact-block {
    position: absolute;
    left: 0; right: 0;
    top: 293px;
    text-align: center;
  }
  .contact-rule {
    width: 112px;
    height: 1px;
    margin: 0 auto;
    background: linear-gradient(90deg, transparent, var(--rule-light), transparent);
  }
  .card--front-black .contact-rule {
    background: linear-gradient(90deg, transparent, var(--rule-dark), transparent);
  }
  .person-name {
    margin-top: 5px;
    font-size: 19px;
    font-weight: 500;
    color: var(--brand-blue);
    line-height: 1.1;
  }
  .person-title {
    font-size: 11px;
    font-weight: 400;
    line-height: 1.3;
  }
  .contact-icons {
    display: flex;
    justify-content: center;
    gap: 5px;
    margin-top: 8px;
    height: 9px;
  }
  .contact-icons svg { width: 9px; height: 9px; }
  .contact-lines {
    margin-top: 6px;
    font-size: 11.5px;
    line-height: 13.5px;
    margin-bottom: 4px;
  }
  .accent { color: var(--brand-blue); }

  .back-url {
    position: absolute;
    left: 0; right: 0;
    top: 396px;
    text-align: center;
    font-size: 12.5px;
    letter-spacing: 1px;
    color: var(--ink-light);
  }
</style>
</head>
<body>

  <section class="card card--front-white">
    <div class="wordmark">quilmora</div>
    <div class="contact-block">
      <div class="contact-rule"></div>
      <div class="person-name">Devin Holt</div>
      <div class="person-title">President</div>
      <div class="contact-icons">
        <svg viewBox="0 0 10 10"><path d="M2 1 L3.5 1 L4 3 L3 3.8 Q4 6 6.2 7 L7 6 L9 6.5 L9 8 Q8.5 9 7.5 9 Q1 8 1 2 Q1 1 2 1 Z" fill="#2ea3dc"/></svg>
        <svg viewBox="0 0 10 10"><rect x="1" y="2.2" width="8" height="5.6" fill="none" stroke="#2ea3dc" stroke-width="1"/><path d="M1 2.5 L5 5.5 L9 2.5" fill="none" stroke="#2ea3dc" stroke-width="1"/></svg>
        <svg viewBox="0 0 10 10"><circle cx="5" cy="5" r="4" fill="none" stroke="#2ea3dc" stroke-width="0.9"/><ellipse cx="5" cy="5" rx="1.8" ry="4" fill="none" stroke="#2ea3dc" stroke-width="0.8"/><path d="M1 5 H9" stroke="#2ea3dc" stroke-width="0.8"/></svg>
      </div>
      <div class="contact-lines">
        <div>(800) 471-2960</div>
        <div>sleep@quilmora.com</div>
        <div>www.quilmora.com</div>
      </div>
      <div class="contact-rule"></div>
    </div>
  </section>

  <section class="card card--back-graphite">
    <div class="wordmark">quilmora</div>
    <div class="back-url">www.quilmora.com</div>
  </section>

  <section class="card card--front-black">
    <div class="wordmark">quilmora</div>
    <div class="contact-block">
      <div class="contact-rule"></div>
      <div class="person-name">Devin Holt</div>
      <div class="person-title">President</div>
      <div class="contact-icons">
        <svg viewBox="0 0 10 10"><path d="M2 1 L3.5 1 L4 3 L3 3.8 Q4 6 6.2 7 L7 6 L9 6.5 L9 8 Q8.5 9 7.5 9 Q1 8 1 2 Q1 1 2 1 Z" fill="#2ea3dc"/></svg>
        <svg viewBox="0 0 10 10"><rect x="1" y="2.2" width="8" height="5.6" fill="none" stroke="#2ea3dc" stroke-width="1"/><path d="M1 2.5 L5 5.5 L9 2.5" fill="none" stroke="#2ea3dc" stroke-width="1"/></svg>
        <svg viewBox="0 0 10 10"><circle cx="5" cy="5" r="4" fill="none" stroke="#2ea3dc" stroke-width="0.9"/><ellipse cx="5" cy="5" rx="1.8" ry="4" fill="none" stroke="#2ea3dc" stroke-width="0.8"/><path d="M1 5 H9" stroke="#2ea3dc" stroke-width="0.8"/></svg>
      </div>
      <div class="contact-lines">
        <div>(800) 471-2960</div>
        <div>sleep@quilmora.com</div>
        <div>www.<span class="accent">quilmora</span>.com</div>
      </div>
      <div class="contact-rule"></div>
    </div>
  </section>

  <section class="card card--back-black">
    <div class="wordmark">quilmora</div>
    <div class="back-url">www.quilmora.com</div>
  </section>

</body>
</html>
```